Exclusive beauty salon needs a price list or services booklet

I need a new very attractive flyer for my beauty salon, containing information on the different services and their prices.
In attachment you can find a pdf of the "old" one, but I'd love to have a beautifully designed new one!
I'd love to have a booklet in format 148 x 148 mm, or in US format, containing 12 or 16 pages, but if you can offer other nice looking designs they are welcome!
The services that need to come in the booklet with their prices can all be found on my website: www.atelierverano.be, starting with
Gelaatsverzorging
Wimperverlenging
Suikerontharing
Wimperlifting
Permanente Make Up
Airbrush Tanning

Target Market(s)

woman from 20 to 89 years old

Industry/Entity Type

Beauty Salon

Font styles to use
Sans Serif

Colors

Designer to choose colors to be used in the design.

Requirements
Must have
• a classy nice look, it must contain details about the services from my beauty salon and their prices, and nice pictures.
• The Names, prices and explanations of the services can easily be found on my website: www.atelierverano.be
Nice to have
• In attachment you can find the "old" price list in pdf, what I need now is a "new booklet" with the new logo and updated services price list.
• I need a very nice and attractive looking booklet, classy chique, Paris chique, looking very expensive.
Should not have
• Not too much colors, not too curly, but still feminine

```html
<!DOCTYPE html>
<html lang="nl">
<head>
<meta charset="utf-8">
<title>Atelier Verano – Prijslijst</title>
<link href="https://fonts.googleapis.com/css2?family=Open+Sans:ital,wght@0,300;0,400;0,600;1,300;1,400&display=swap" rel="stylesheet">
<style>
:root{
  --stage:#5f5f5f;
  --frame:#a3a6a9;
  --paper:#ffffff;
  --teal:#4bb3c1;
  --ink:#707478;
  --ink-soft:#8b8f93;
  --mint:#9fcdc0;
  --dark:#1f1f1f;
}
*{margin:0;padding:0;box-sizing:border-box}
html,body{width:1122px;height:1200px;overflow:hidden;background:var(--stage)}
body{position:relative;font-family:"Open Sans",Arial,sans-serif;color:var(--ink)}
.spread{position:absolute;width:533px;height:380px;background:var(--frame)}
.spread.light{background:var(--paper)}
.page{position:absolute;left:21px;top:21px;width:490px;height:338px;background:var(--paper);overflow:hidden}
.photo{position:absolute;top:0;height:100%}
.copy{position:absolute;top:0;height:100%;padding:14px 16px}
h2{font-weight:400;color:var(--teal);font-size:11.5px;margin:0 0 5px}
p,li{font-style:italic;font-weight:300;font-size:6.6px;line-height:1.45;color:var(--ink);text-align:justify}
.price{display:block;text-align:right;color:var(--teal);font-style:italic;font-size:10px;margin:3px 0 8px}
ul{list-style:none}
li{position:relative;padding-left:9px;text-align:left}
li::before{content:"✓";position:absolute;left:0;color:var(--teal);font-style:normal}
.brand{position:absolute;left:0;bottom:0;width:236px;height:42px;background:var(--paper);display:flex;align-items:center;justify-content:center;font-size:21px;font-weight:600;color:var(--dark);letter-spacing:2px}
.rates{list-style:none;margin-top:4px}
.rates div{display:flex;justify-content:space-between;font-style:italic;font-weight:300;font-size:9.4px;color:var(--ink);line-height:16.3px;width:210px}
.rates span:last-child{color:var(--teal)}
.rates small{font-size:7px}
.studio{position:absolute;left:70px;bottom:14px;text-align:center;font-size:9px;letter-spacing:5px;color:var(--dark)}
.studio b{display:block;font-weight:400;font-size:17px;letter-spacing:4px;margin-bottom:4px}
.box{position:absolute;border:1px solid #d9dbdd;padding:10px 12px}
.box p,.box li{color:#fff;font-size:7px}
.box li::before{color:#fff}
.offer{position:absolute;left:0;width:100%;text-align:center;color:#fff;font-size:12.5px;line-height:20px;font-weight:300}
.tag{position:absolute;left:20px;bottom:14px;width:176px;height:104px;background:var(--mint);opacity:.92;color:#fff;font-size:17px;font-weight:300;text-align:center;display:flex;align-items:center;justify-content:center;line-height:25px}
.corner-mark{position:absolute;right:14px;top:24px;color:rgba(255,255,255,.8);font-size:7px;letter-spacing:3px}
</style>
</head>
<body>

<!-- Spread 1: facial care -->
<section class="spread" style="left:20px;top:12px">
  <div class="page">
    <div class="photo" style="left:0;width:236px;background:linear-gradient(160deg,#e9dcd4,#f4ece7 55%,#efe6e1)" role="img" aria-label="Portret van een glimlachende vrouw met de hand op de wang"></div>
    <div class="brand">ORÉLIE</div>
    <div class="copy" style="left:236px;width:254px">
      <h2>Gelaatsverzorging Orélie</h2>
      <p>Het merk Orélie heeft een uitgebreid aanbod aan gelaatsverzorgingen, geschikt voor alle "huidproblemen". Na een persoonlijke huidanalyse wordt een verzorging uitgevoerd die bij u past. Naast de cabineverzorgingen, kan je ook advies krijgen voor de dagelijkse verzorging thuis.<br>Gelaatsverzorgingen van Orélie bieden:</p>
      <ul style="margin:1px 0 8px 16px"><li>Een combinatie van plezier en welzijn</li><li>Een unieke ervaring voor de zintuigen</li><li>Resultaatgerichte behandelingen</li></ul>
      <h2>Cosmetische Verzorging</h2>
      <p>Verzorging i.o.v. Dermatoloog. De verzorging bestaat uit: oppervlakkige reiniging, verwijderen zwarte puntjes en onzuiverheden, zuiverend masker.</p>
      <span class="price">€30</span>
      <h2>Verwijderen van gerstekorrels</h2>
      <p>De prijs is afhankelijk van de hoeveelheid.</p>
      <span class="price">Vanaf €15</span>
      <h2>Flash Nettoyant</h2>
      <p>Voor een gehydrateerde en comfortabele huid. Voor alle huidtypes, bij een vermoeide huid met weinig uitstraling. De verzorging bestaat uit: epilatie wenkbrauwen, oppervlakkige reiniging, diepe reiniging, cremem asker aangepast aan huidconditie, serum, dagcème, handmassage.</p>
      <span class="price" style="margin:0">€59 - 50 min.</span>
    </div>
  </div>
</section>

<!-- Spread 2: treatments -->
<section class="spread" style="left:571px;top:12px">
  <div class="page">
    <div class="copy" style="left:0;width:252px;padding-left:18px">
      <h2>Hydratation Essentielle</h2>
      <p>Voor een gehydrateerde, volle en frisse huid. Geschikt voor alle huidtypes. De verzorging bestaat uit: epilatie wenkbrauwen, oppervlakkige reiniging, diepe reiniging, verwijderen van comedonen, massage van gelaat en décolleté, instituutmasker aangepast aan huidconditie, serum, dagcème, handmassage.</p>
      <span class="price">€65- 60 min.</span>
      <h2>Pureté Essentielle</h2>
      <p>Voor een gezonde en gezuiverde matte huid. Voor gemengde tot vette huidtypes, met of zonder onzuiverheden. De verzorging bestaat uit: epilatie wenkbrauwen, oppervlakkige reiniging, diepe reiniging, verwijderen van comedonen, massage van gelaat en décolleté, instituutmasker aangepast aan huidconditie, serum, dagcème, handmassage.</p>
      <span class="price">€65 - 60 min.</span>
      <h2>Luxe Verzorging Suprême Expérience</h2>
      <p>Luxe gelaatsverzorging voor een herstelde, stralende huid met gladde trekken. De verzorging bestaat uit: epilatie wenkbrauwen, oppervlakkige reiniging, diepe reiniging, verwijderen van comedonen, voorbereidend masker, massage van gelaat en décolleté, instituutmasker aangepast aan huidconditie met extra anti aging actieve werkstoffen, serum, dagcème, handmassage.</p>
      <span class="price">€85 - 80 min.</span>
    </div>
    <div class="photo" style="right:0;width:237px;background:linear-gradient(200deg,#f3d9df,#f1e3e3 50%,#e9d5d0)" role="img" aria-label="Portret van een vrouw met donker opgestoken haar"></div>
  </div>
</section>

<!-- Spread 3: sugaring -->
<section class="spread" style="left:20px;top:410px">
  <div class="page">
    <div class="photo" style="left:0;width:236px;background:linear-gradient(170deg,#fbfbfb 0%,#e8b89a 40%,#dba07c 70%,#f0e9e8 100%)" role="img" aria-label="Suikerpasta wordt op een been aangebracht, rozenblaadjes op een handdoek"></div>
    <div class="copy" style="left:236px;width:254px;padding:14px 14px 14px 22px">
      <h2>Ontharing Met Suiker</h2>
      <p style="text-align:left">Heb je ook genoeg van lichaams- en/of gezichtsbeharing maar ben je niet tevreden met het resultaat van scheren/harsen/laseren? Dan is ontharen met suiker van Sucrelle dé oplossing!<br>De voordelen van ontharen met suiker:</p>
      <ul style="margin-top:8px">
        <li style="margin-bottom:4px">De haren worden met de haargroeirichting verwijderd, hierdoor vermindert de pijn en je hebt geen last van haartjes die afbreken</li>
        <li style="margin-bottom:4px">De haren worden volledig verwijderd (met de haarwortel) waardoor ze dunner en donziger worden en minder snel aangroeien</li>
        <li style="margin-bottom:4px">Er wordt hygiënisch gewerkt</li>
        <li style="margin-bottom:4px">De huidstructuur verbetert door het verwijderen van dode huidcellen zonder de levende cellen te beschadigen</li>
        <li style="margin-bottom:4px">Suiker bestaat uit lichaamseigen stoffen waardoor de huid minder fel reageert op de ontharing.</li>
        <li style="margin-bottom:4px">Suikerontharing zorgt ervoor dat de haargroei vermindert na iedere behandeling en verfijnt de haarstructuur</li>
        <li style="margin-bottom:4px">Met suikerontharing werkt men op lichaamstemperatuur dus geen brandwonden</li>
        <li style="margin-bottom:4px">Suikerontharing is geschikt voor de couperose huid en is uiterst geschikt voor de meest gevoelige plaatsen (bikini, gezicht,...)</li>
        <li>Suiker is wateroplosbaar, dus geen ongewenste plakseltjes</li>
      </ul>
    </div>
  </div>
</section>

<!-- Spread 4: rates -->
<section class="spread" style="left:571px;top:410px">
  <div class="page">
    <div class="copy" style="left:0;width:253px;padding:14px 18px">
      <h2 style="margin-bottom:6px">TARIEVEN</h2>
      <div class="rates">
        <div><span>Wenkbrauwen</span><span>€9</span></div>
        <div><span>Wenkbrauwen en bovenlip</span><span>€16</span></div>
        <div><span>Bovenlip of kin</span><span>€9</span></div>
        <div><span>Bovenlip en kin</span><span>€16</span></div>
        <div><span>Gezicht <small>(bovenlip, kin, wangen en wenkbrauw)</small></span><span>€25</span></div>
        <div><span>Oksels</span><span>€12</span></div>
        <div><span>Armen</span><span>€20</span></div>
        <div><span>Brazilian bikini of string</span><span>€30</span></div>
        <div><span>Bikinilijn</span><span>€15</span></div>
        <div><span>Onderbeen en knie</span><span>€30</span></div>
        <div><span>Bovenbenen</span><span>€20</span></div>
        <div><span>Volledige benen (zonder bikini)</span><span>€50</span></div>
        <div><span>volledige benen incl. Bikinilijn</span><span>€59</span></div>
      </div>
      <div class="studio" style="left:0;width:253px"><b>ATELIER VERANO</b>SCHOONHEIDSINSTITUUT</div>
    </div>
    <div class="photo" style="right:0;width:237px;background:linear-gradient(180deg,#f6f3f1 0%,#e9c08c 35%,#d99d6f 65%,#f2efec 100%)" role="img" aria-label="Suikerpasta druipt van een spatel in een pot op een schouder"></div>
  </div>
</section>

<!-- Spread 5: lash info -->
<section class="spread light" style="left:20px;top:806px">
  <div class="page" style="background:var(--frame)">
    <div class="box" style="left:37px;top:62px;width:197px;height:192px">
      <p>Lange, volle en gekrulde wimpers dankzij Cilia Line. Zijden wimpers worden één per één op uw eigen wimpers gekleefd. Mascara kan maar is overbodig. Cilia Line wimpers zijn ultralicht en zoveel natuurlijker dan kunststoffen wimperstrips, stukjes en plukjes. Door de exclusief ontwikkelde lijm blijven ze wekenlang in positie. De sneldrogende lijm laat een plaatsing toe van ongeveer 60 wimpers per oog. Een vol effect, in een behandeling van slechts 1/2 uur.</p>
      <p style="margin-top:4px">Na max. 4 weken laten bijwerken garandeert een optimaal en schitterend eindresultaat.</p>
      <p style="margin-top:4px">De zijden wimpers zijn beschikbaar in verschillende lengtes, diktes en krulling of curves.</p>
    </div>
    <div class="box" style="left:255px;top:62px;width:197px;height:192px">
      <p style="text-align:left;margin-bottom:4px">Voordelen van Cilia Line Wimperverlenging op een rijtje</p>
      <ul>
        <li style="margin-bottom:2px">Pijnloze behandeling</li>
        <li style="margin-bottom:2px">Geen beschadiging van de natuurlijke wimpers</li>
        <li style="margin-bottom:2px">Onmiddellijk een verbluffend resultaat</li>
        <li style="margin-bottom:2px">Geen nazorg</li>
        <li style="margin-bottom:2px">Verkrijgbaar in verschillende lengtes, diktes en curves</li>
        <li style="margin-bottom:2px">Prima oplossing voor feestjes, vakanties, enz.</li>
        <li style="margin-bottom:2px">Mascara wordt overbodig</li>
        <li style="margin-bottom:2px">Wimperextensions blijven aangehecht tijdens het zwemmen, douchen en saunabezoek</li>
        <li>Cilia Line garandeert wekenlang plezier</li>
      </ul>
    </div>
    <div class="offer" style="top:270px">Eerste plaatsing wimperextensions €65<br>Bijwerking na max. 4 weken €35</div>
  </div>
</section>

<!-- Spread 6: lash cover -->
<section class="spread light" style="left:571px;top:806px">
  <div class="page">
    <div class="photo" style="left:0;width:100%;background:linear-gradient(120deg,#e9b79c 0%,#f2c9b2 40%,#f6e0d4 70%,#e7a98d 100%)" role="img" aria-label="Close-up van wimperverlenging met pincetten bij een gesloten oog"></div>
    <div class="corner-mark">ATELIER VERANO</div>
    <div class="tag">Individuele<br>Wimperverlenging<br>Cilia Line</div>
  </div>
</section>

</body>
</html>
```